New Business Card Design Project

Use the flyer uploaded and website www.brightoakbuilders.com for inspiration.
List Our Services on Backside of business cards
Marcus Delling
Harborline Builders Inc.
Licensed General Contractors
858-471-6093

Contact Information for Business Card

Use the flyer uploaded and website www.brightoakbuilders.com for inspiration. List Our Services on Backside of business cards Marcus Delling Harborline Builders Inc. Licensed General Contractors 858-471-6093

```html
<!DOCTYPE html>
<html lang="en">
<head>
<meta charset="utf-8">
<title>Harborline Builders – Business Card</title>
<link href="https://fonts.googleapis.com/css2?family=Montserrat:wght@400;600;700;800&display=swap" rel="stylesheet">
<style>
  :root {
    --stage: #3a3a3a;
    --card: #141414;
    --ink: #ffffff;
    --ink-soft: #e6e6e6;
  }
  * { margin: 0; padding: 0; box-sizing: border-box; }
  html, body { width: 1200px; height: 998px; overflow: hidden; background: var(--stage); }
  body { font-family: "Montserrat", sans-serif; color: var(--ink); position: relative; }

  .card {
    position: absolute;
    left: 200px;
    width: 800px;
    height: 457px;
    background: var(--card);
    box-shadow: 0 10px 28px rgba(0,0,0,.45);
  }
  .card--back { top: 28px; }
  .card--front { top: 513px; }

  .brand-name {
    position: absolute;
    font-family: "Montserrat", sans-serif;
    font-weight: 400;
    letter-spacing: 2px;
    text-transform: uppercase;
    color: var(--ink);
    font-size: 24px;
    white-space: nowrap;
  }
  .card--back .brand-name { left: 50px; top: 248px; }
  .card--front .brand-name { right: 50px; top: 120px; }

  .services { position: absolute; left: 450px; top: 110px; }
  .services__title { font-weight: 800; font-size: 21px; letter-spacing: .5px; margin-bottom: 6px; }
  .services__list { list-style: none; }
  .services__item {
    display: flex; align-items: center; gap: 9px;
    font-size: 17px; line-height: 27px; color: var(--ink-soft);
    white-space: nowrap;
  }
  .services__item svg { flex: none; }

  .contact-name { position: absolute; left: 56px; top: 262px; font-weight: 700; font-size: 40px; }
  .contact-role { position: absolute; left: 56px; top: 314px; font-weight: 700; font-size: 19px; }
  .divider { position: absolute; left: 56px; right: 50px; top: 352px; height: 1.5px; background: var(--ink); }
  .contact-line {
    position: absolute; top: 376px;
    display: flex; align-items: center; gap: 10px;
    font-size: 20px; font-weight: 400;
  }
  .contact-line--phone { left: 56px; }
  .contact-line--web { right: 50px; }
</style>
</head>
<body>

<section class="card card--back" aria-label="Card back">
  <div class="brand-name">Harborline Builders</div>

  <div class="services">
    <h2 class="services__title">OUR SERVICES</h2>
    <ul class="services__list">
      <li class="services__item"><svg width="16" height="16" viewBox="0 0 16 16"><rect x="1" y="1" width="14" height="14" fill="none" stroke="#fff" stroke-width="1.8"/><path d="M4 8l3 3 5-6" fill="none" stroke="#fff" stroke-width="2"/></svg>Remodel: Kithcen &amp; Bath</li>
      <li class="services__item"><svg width="16" height="16" viewBox="0 0 16 16"><rect x="1" y="1" width="14" height="14" fill="none" stroke="#fff" stroke-width="1.8"/><path d="M4 8l3 3 5-6" fill="none" stroke="#fff" stroke-width="2"/></svg>Painting: Interior &amp; Exterior</li>
      <li class="services__item"><svg width="16" height="16" viewBox="0 0 16 16"><rect x="1" y="1" width="14" height="14" fill="none" stroke="#fff" stroke-width="1.8"/><path d="M4 8l3 3 5-6" fill="none" stroke="#fff" stroke-width="2"/></svg>Flooring: Carpet, Vinyl, Wood</li>
      <li class="services__item"><svg width="16" height="16" viewBox="0 0 16 16"><rect x="1" y="1" width="14" height="14" fill="none" stroke="#fff" stroke-width="1.8"/><path d="M4 8l3 3 5-6" fill="none" stroke="#fff" stroke-width="2"/></svg>Window &amp; Door Replacement</li>
      <li class="services__item"><svg width="16" height="16" viewBox="0 0 16 16"><rect x="1" y="1" width="14" height="14" fill="none" stroke="#fff" stroke-width="1.8"/><path d="M4 8l3 3 5-6" fill="none" stroke="#fff" stroke-width="2"/></svg>Plumbing: Repairs &amp; Upgrades</li>
      <li class="services__item"><svg width="16" height="16" viewBox="0 0 16 16"><rect x="1" y="1" width="14" height="14" fill="none" stroke="#fff" stroke-width="1.8"/><path d="M4 8l3 3 5-6" fill="none" stroke="#fff" stroke-width="2"/></svg>Energy- Efficient Upgrades</li>
      <li class="services__item"><svg width="16" height="16" viewBox="0 0 16 16"><rect x="1" y="1" width="14" height="14" fill="none" stroke="#fff" stroke-width="1.8"/><path d="M4 8l3 3 5-6" fill="none" stroke="#fff" stroke-width="2"/></svg>Deck &amp; Patio Construction</li>
    </ul>
  </div>
</section>

<section class="card card--front" aria-label="Card front">
  <div class="brand-name">Harborline Builders</div>

  <div class="contact-name">Marcus Delling</div>
  <div class="contact-role">Licensed General Contractors</div>
  <div class="divider"></div>

  <div class="contact-line contact-line--phone">
    <svg width="20" height="20" viewBox="0 0 24 24"><circle cx="12" cy="12" r="11" fill="#fff"/><path d="M8 6.5c.6-.5 1.3-.4 1.6.2l1 2c.2.5 0 1-.4 1.3l-.7.5c.6 1.4 1.6 2.5 3 3.2l.6-.6c.4-.4.9-.5 1.3-.3l2 1c.6.3.7 1 .3 1.6l-.8 1c-.6.7-1.6.9-2.5.5-3.2-1.4-5.5-3.8-6.600-7-.3-.9 0-1.9.7-2.4z" fill="#141414"/></svg>
    <span>858-471-6093</span>
  </div>

  <div class="contact-line contact-line--web">
    <svg width="20" height="20" viewBox="0 0 24 24" fill="none" stroke="#fff" stroke-width="2"><circle cx="12" cy="12" r="10"/><ellipse cx="12" cy="12" rx="4.5" ry="10"/><path d="M2 12h20M4 7h16M4 17h16"/></svg>
    <span>www.brightoakbuilders.com</span>
  </div>
</section>

</body>
</html>
```